Velkora Land Surveying Website Design

We are working with Velkora. They are a national land surveying company and in need of a new website design.

Some sites to use for inspiration:

https://brannickeng.com
https://www.dvwinc.com
https://kelvarin.com
https://gto.us
https://ravendobuilt.com
https://www.marbeckquillondale.com

Thank you for taking the time to consider designing a website for us. We are web developers based in Stockton and Los Angeles, CA, USA. Most of our projects go through the same process. Understanding this process may help you win a project with us. We custom-code all of our websites in-house. We don’t have any requirements as to what tools you use for your design, but we prefer Figma files. For any design that we label as four-stars, we send it to the client for review. The client picks the final design they want us to use. Once we complete this process, we will continue to show additional clients all the four-star sites and purchase them later. Your designs will have multiple chances to sell. For better chances of success, we ask that you follow these guidelines.

IMAGES:
If you use any images or icons in the design, we ask that you have a link to the asset so we can purchase the image/icon. Most of the designs we submit do not have the customer’s images on them unless they have some great images. Be creative; show us the feeling you are trying to portray with your image choices. Use any royalty-free site you choose. We subscribe to Pellix and mainly use their images, but we can purchase images outside of Pellix.

PLEASE NOTE: we will not submit designs to clients with watermarks on the images.

FONTS:
We ask that you identify the fonts used in the design. This can be done in a message if you want. We typically use Google Fonts and Pellix Fonts.

CONTENT:
We're always open to different content and ideas. We often submit designs with stock images so the client can see our vision. We typically take pictures after the website launch to use their images with our vision. Lorem Ipsum is fine for paragraphs, but we ask that you write the headers in correct English. We want to be able to show the vision and identify the sections of the website.

INSPIRATION:
We typically add a couple of links in the brief of websites we like to help you get started in your design.

REVISIONS:
We do not often ask for revisions of the designs unless we see something in the design that may not appeal to the client. If there are slight changes that we want to make, we do that in the development process.

FEEDBACK:
We rarely give feedback on designs during the design process. We are working on many website projects and do not have the time to provide feedback. We usually respond if your request is well thought out and asks specific questions, but a note asking “feedback, please” usually goes unanswered.

```html
<!DOCTYPE html>
<html lang="en">
<head>
<meta charset="utf-8">
<title>Velkora Land Surveying</title>
<link rel="stylesheet" href="https://fonts.googleapis.com/css2?family=Saira:wght@400;500;600&family=Figtree:wght@400;500;600&display=swap">
<style>
:root{
  --red:#e04a3b;
  --ink:#222;
  --muted:#444;
  --gray:#7b7b7b;
  --dark:#262626;
  --white:#fff;
  --head:"Saira",sans-serif;
  --body:"Figtree",sans-serif;
}
*{box-sizing:border-box;margin:0;padding:0}
html,body{width:1200px;height:3393px;overflow:hidden}
body{position:relative;background:var(--white);font-family:var(--body);color:var(--ink)}
.abs{position:absolute}
a{color:inherit;text-decoration:none}

/* top bar */
.topbar{top:0;left:0;width:1200px;height:48px;font-size:13px;color:var(--ink)}
.topbar .item{top:16px;display:flex;align-items:center;gap:8px}
.topbar .lbl{color:var(--red)}
.nav{left:99px;top:47px;width:1002px;height:80px;background:var(--white);box-shadow:0 2px 12px rgba(0,0,0,.12);z-index:3}
.brand{left:24px;top:18px;display:flex;align-items:center;gap:10px}
.brand .mark{width:40px;height:40px;border-radius:50%;background:var(--red)}
.brand .name{font-family:var(--head);font-weight:600;font-size:24px;line-height:1;color:var(--red);letter-spacing:.5px}
.brand .sub{font-family:var(--head);font-size:10px;letter-spacing:2px;color:var(--gray)}
.menu{left:258px;top:30px;display:flex;gap:33px;font-size:14px;font-weight:500}
.menu .on{color:var(--red)}
.quote{right:18px;top:19px;width:172px;height:42px;background:var(--red);color:#fff;font-size:14px;font-weight:500;display:flex;align-items:center;justify-content:center}

/* hero */
.hero{top:87px;left:0;width:1200px;height:513px;background:linear-gradient(100deg,#5b5338 0%,#8a7a52 35%,#7d7350 60%,#6d6d5a 100%)}
.hero .photo-worker{left:60px;top:40px;width:420px;height:473px;background:linear-gradient(180deg,#cfcfcf 0%,#9aa046 45%,#c9a23a 100%);border-radius:120px 120px 0 0;opacity:.85}
.hero h1{left:520px;top:125px;width:625px;text-align:center;font-family:var(--head);font-weight:500;font-size:45px;line-height:61px;color:#fff}
.hero p{left:510px;top:262px;width:645px;text-align:center;font-size:17px;line-height:37px;color:#fff}
.btn{background:var(--red);color:#fff;font-size:14px;font-weight:500;display:flex;align-items:center;justify-content:center}
.hero .btn{left:747px;top:367px;width:171px;height:41px}

/* services */
.sec-title{font-family:var(--head);font-weight:500;font-size:45px;color:#5a5a5a}
.sec-title span{color:var(--red)}
.services-title{left:109px;top:668px}
.services-intro{left:591px;top:675px;width:510px;font-size:15px;line-height:34px;color:var(--muted)}
.card{top:823px;width:318px;height:468px;background:#fff;box-shadow:0 1px 8px rgba(0,0,0,.14);text-align:center}
.card h3{position:absolute;left:20px;top:27px;width:278px;font-weight:400;font-size:17px;line-height:33px;color:var(--red)}
.card p{position:absolute;left:22px;top:100px;width:274px;font-size:15px;line-height:33.5px;color:var(--ink)}
.card .img{position:absolute;left:14px;top:264px;width:290px;height:190px}
.card.active{background:var(--red)}
.card.active h3,.card.active p{color:#fff}
.arrow{width:20px;height:20px}

/* about */
.about{top:1376px;left:0;width:1200px;height:514px;background:var(--gray)}
.about .redband{left:898px;top:0;width:302px;height:514px;background:var(--red)}
.about h2{left:109px;top:56px;font-family:var(--head);font-weight:500;font-size:45px;color:#fff}
.about p{left:109px;top:132px;width:420px;font-size:15px;line-height:34.3px;color:#fff}
.about .btn{left:109px;top:399px;width:140px;height:40px}
.about .img{left:599px;top:54px;width:390px;height:406px;background:linear-gradient(180deg,#c9d6e3 0%,#9aa9b4 35%,#5e6b46 60%,#3e4a2f 100%)}

/* insights */
.insights-title{left:0;top:1953px;width:1200px;text-align:center}
.post-card{left:112px;top:2061px;width:407px;height:439px;background:#fff;box-shadow:0 1px 8px rgba(0,0,0,.14)}
.post-card .img{left:14px;top:17px;width:377px;height:232px;background:linear-gradient(180deg,#a9c6e0 0%,#c8c49a 40%,#8c8450 100%)}
.date{background:var(--red);color:#fff;font-size:17px;display:flex;align-items:center;justify-content:center}
.post-card .date{left:43px;top:231px;width:151px;height:36px}
.post-title{font-family:var(--head);font-weight:500;font-size:20px;line-height:40px;color:var(--ink)}
.more{font-size:17px;font-weight:500;color:var(--red);text-decoration:underline;text-underline-offset:3px;letter-spacing:.5px}
.post-card .post-title{left:26px;top:292px;width:370px}
.post-card .more{left:26px;top:383px}
.post-side .date{width:150px;height:37px}

/* projects */
.projects-title{left:0;top:2568px;width:1200px;text-align:center}
.footer{left:0;top:2994px;width:1200px;height:399px;background:var(--dark)}
.project-img{left:112px;top:2676px;width:976px;height:411px;background:linear-gradient(180deg,#c7cfc8 0%,#6d7a5a 35%,#3f6a2e 65%,#56833a 100%);z-index:2}
.project-cap{left:749px;top:2702px;width:339px;height:103px;background:#fff;z-index:3;font-family:var(--head);font-weight:500;font-size:21px;line-height:37px;color:var(--ink);padding:14px 0 0 29px}

/* footer */
.footer .brand{left:119px;top:140px}
.footer .brand .sub{color:#aaa}
.copy{left:119px;top:240px;font-size:14px;color:#fff;font-weight:500}
.foot-h{font-size:19px;font-weight:500;color:var(--red)}
.foot-links{font-size:14px;font-weight:500;color:#fff;line-height:37.5px}
.contact-row{display:flex;align-items:center;gap:12px;font-size:14px;font-weight:500;color:#fff}
</style>
</head>
<body>

<header>
  <div class="abs topbar">
    <div class="abs item" style="left:112px">
      <svg width="15" height="15" viewBox="0 0 24 24"><path fill="#e04a3b" d="M6.6 10.8a15 15 0 0 0 6.6 6.6l2.2-2.2a1 1 0 0 1 1-.25 11.4 11.4 0 0 0 3.6.57 1 1 0 0 1 1 1V20a1 1 0 0 1-1 1A17 17 0 0 1 3 4a1 1 0 0 1 1-1h3.5a1 1 0 0 1 1 1c0 1.25.2 2.45.57 3.57a1 1 0 0 1-.25 1z"/></svg>
      <span><span class="lbl">CALL US :</span> (800) 555-3918</span>
    </div>
    <div class="abs item" style="right:112px">
      <svg width="16" height="12" viewBox="0 0 16 12"><rect width="16" height="12" fill="#e04a3b"/><path d="M0 0l8 6 8-6" stroke="#fff" stroke-width="1.4" fill="none"/></svg>
      <span><span class="lbl">MAIL US :</span> INFO@VELKORASURVEY.COM</span>
    </div>
  </div>

  <nav class="abs nav">
    <div class="abs brand">
      <div class="mark"></div>
      <div><div class="name">VELKORA</div><div class="sub">LAND SURVEYING</div></div>
    </div>
    <div class="abs menu">
      <a class="on">HOME</a><a>ABOUT</a><a>SERVICES</a><a>PROJECTS</a><a>CAREERS</a><a>INSIGHTS</a>
    </div>
    <a class="abs quote">REQUEST A QUOTE</a>
  </nav>
</header>

<section class="abs hero">
  <div class="abs photo-worker" role="img" aria-label="Surveyor in hard hat and safety vest using a total station over open farmland"></div>
  <h1 class="abs">National Land Surveying.<br>Precise. Trusted.</h1>
  <p class="abs">Delivering accurate, code-compliant, and visually impactful surveying solutions for commercial, residential, and infrastructure projects nationwide.</p>
  <a class="abs btn">GET STARTED NOW</a>
</section>

<section>
  <h2 class="abs sec-title services-title">Our <span>Services</span></h2>
  <p class="abs services-intro">From boundary surveys to advanced 3D LiDAR scanning, we provide accurate data to keep your projects on track, built on precision, compliance, and trust.</p>

  <svg class="abs arrow" style="left:32px;top:1046px" viewBox="0 0 20 20"><path d="M13 3l-7 7 7 7" stroke="#111" stroke-width="2.4" fill="none"/></svg>
  <svg class="abs arrow" style="left:1138px;top:1046px" viewBox="0 0 20 20"><path d="M7 3l7 7-7 7" stroke="#111" stroke-width="2.4" fill="none"/></svg>

  <article class="abs card" style="left:103px">
    <h3>BOUNDARY &amp; TOPOGRAPHIC SURVEYS</h3>
    <p>Define property lines and terrain features with precise measurements for development, design, and compliance.</p>
    <div class="img" role="img" aria-label="Surveyor kneeling beside a tripod on a dirt site" style="background:linear-gradient(180deg,#6f6a60 0%,#8e7a62 60%,#5a4f44 100%)"></div>
  </article>
  <article class="abs card active" style="left:441px">
    <h3>ALTA / NSPS LAND TITLE SURVEYS</h3>
    <p>Industry-standard surveys for commercial real estate transactions, ensuring accuracy and regulatory compliance.</p>
    <div class="img" role="img" aria-label="Hand marking a survey plan with a pencil outdoors" style="background:linear-gradient(180deg,#8fb0cf 0%,#9aa27a 40%,#e5e8ea 70%,#cfd6dd 100%)"></div>
  </article>
  <article class="abs card" style="left:778px">
    <h3>CONSTRUCTION LAYOUT &amp; STAKING</h3>
    <p>Accurate placement of foundations, utilities, and structural elements to keep projects on schedule and within spec.</p>
    <div class="img" role="img" aria-label="Tripod over a graded site with layout lines" style="background:linear-gradient(180deg,#b0875e 0%,#c79a6c 55%,#a9835e 100%)"></div>
  </article>
</section>

<section class="abs about">
  <div class="abs redband"></div>
  <h2 class="abs">About Velkora</h2>
  <p class="abs">At Velkora, we are more than a land surveying company—we are a trusted partner in shaping the built environment. With decades of combined experience, our team delivers accurate, code-compliant, and visually clear surveying solutions that help clients build with confidence. As a nationally recognized firm, we support projects of every scale, from commercial developments</p>
  <a class="abs btn">LEARN MORE</a>
  <div class="abs img" role="img" aria-label="Aerial view of farmland parcels with boundary markers and a valley town"></div>
</section>

<section>
  <h2 class="abs sec-title insights-title">Latest <span>Insights</span></h2>

  <article class="abs post-card">
    <div class="abs img" role="img" aria-label="Two surveyors with equipment in a grassy field"></div>
    <div class="abs date">23TH AUG 2025</div>
    <h3 class="abs post-title">The Future of Surveying: How Drones and LiDAR Are Changing the Industry</h3>
    <a class="abs more">LEARN MORE</a>
  </article>

  <article class="post-side">
    <div class="abs date" style="left:585px;top:2062px">23TH AUG 2025</div>
    <h3 class="abs post-title" style="left:585px;top:2124px;width:520px">ALTA/NSPS Land Title Surveys: Why Accuracy Matter in Commercial Real Estate</h3>
    <a class="abs more" style="left:585px;top:2215px">LEARN MORE</a>
  </article>
  <article class="post-side">
    <div class="abs date" style="left:585px;top:2293px">23TH AUG 2025</div>
    <h3 class="abs post-title" style="left:585px;top:2355px;width:520px">Boundary vs. Topographic Surveys: Which One Does Your Project Need?</h3>
    <a class="abs more" style="left:585px;top:2446px">LEARN MORE</a>
  </article>
</section>

<section>
  <h2 class="abs sec-title projects-title">Our <span>Projects</span></h2>
  <svg class="abs arrow" style="left:32px;top:2847px" viewBox="0 0 20 20"><path d="M13 3l-7 7 7 7" stroke="#111" stroke-width="2.4" fill="none"/></svg>
  <svg class="abs arrow" style="left:1138px;top:2847px" viewBox="0 0 20 20"><path d="M7 3l7 7-7 7" stroke="#111" stroke-width="2.4" fill="none"/></svg>
  <div class="abs project-img" role="img" aria-label="Landscaped courtyard with paved walkways beside an office building"></div>
  <div class="abs project-cap">Commercial Development –<br>Downtown Office Complex</div>
</section>

<footer class="abs footer">
  <div class="abs brand">
    <div class="mark"></div>
    <div><div class="name">VELKORA</div><div class="sub">LAND SURVEYING</div></div>
  </div>
  <div class="abs copy">©2025 COPYRIGHTS</div>

  <div class="abs foot-h" style="left:481px;top:142px">QUICK LINKS</div>
  <div class="abs foot-links" style="left:481px;top:177px">
    <div>ABOUT</div><div>SERVICES</div><div>PROJECTS</div><div>CAREERS</div><div>INSIGHTS</div>
  </div>

  <div class="abs foot-h" style="left:776px;top:142px">CONTACT US</div>
  <div class="abs contact-row" style="left:776px;top:194px">
    <svg width="14" height="14" viewBox="0 0 24 24"><path fill="#fff" d="M6.6 10.8a15 15 0 0 0 6.6 6.6l2.2-2.2a1 1 0 0 1 1-.25 11.4 11.4 0 0 0 3.6.57 1 1 0 0 1 1 1V20a1 1 0 0 1-1 1A17 17 0 0 1 3 4a1 1 0 0 1 1-1h3.5a1 1 0 0 1 1 1c0 1.25.2 2.45.57 3.57a1 1 0 0 1-.25 1z"/></svg>
    <span>CALL US : (800) 555-3918</span>
  </div>
  <div class="abs contact-row" style="left:776px;top:244px">
    <svg width="16" height="12" viewBox="0 0 16 12"><rect width="16" height="12" fill="#fff"/><path d="M0 0l8 6 8-6" stroke="#262626" stroke-width="1.4" fill="none"/></svg>
    <span>MAIL US : INFO@VELKORASURVEY.COM</span>
  </div>
</footer>

</body>
</html>
```